Business Card Design Project

I require a business card with the following information on them for various different people;
name
m:
f:
e:
I have a logo already and will attached that. We are in the construction industry. I require something clean and simple but eye catching at the same time. You can use another colour with our logo if you like and you can style the logo as well if you wish. I am open.
Also it needs to be front and back design.
Industry/Entity Type
Construction
Requirements
Must have
- Logo, name, mobile, fax and email address.
Front and back design

```html
<!DOCTYPE html>
<html lang="en">
<head>
<meta charset="utf-8">
<title>Stonebridge Builders – Business Card</title>
<link rel="stylesheet" href="https://fonts.googleapis.com/css2?family=Source+Sans+3:wght@400;600;700&display=swap">
<style>
  :root {
    --backdrop: #a97f24;
    --card-white: #ffffff;
    --green-light: #b6dd58;
    --green-mid: #8ccb3e;
    --green-deep: #58a927;
    --green-glow: #c6e764;
    --brand-green: #5aaa28;
    --text-light: #ffffff;
  }
  * { box-sizing: border-box; margin: 0; padding: 0; }
  html, body {
    width: 1200px; height: 686px; overflow: hidden;
    background: var(--backdrop);
    font-family: "Source Sans 3", sans-serif;
  }
  .canvas { position: relative; width: 1200px; height: 686px; }
  .card {
    position: absolute; width: 510px; height: 291px;
    border-radius: 13px; overflow: hidden;
  }
  .card-front { left: 67px; top: 116px; background: var(--card-white); }
  .card-back {
    left: 621px; top: 303px;
    background: radial-gradient(ellipse at 50% 48%, var(--green-glow) 0%, var(--green-mid) 60%, var(--green-deep) 100%);
    display: flex; align-items: center; justify-content: center;
  }
  .front-panel { position: absolute; inset: 0; width: 510px; height: 291px; }
  .brand {
    position: absolute; left: 52px; top: 130px;
    display: flex; align-items: center; gap: 10px;
  }
  .brand-mark { width: 22px; height: 22px; background: var(--brand-green); }
  .brand-name {
    font-size: 25px; font-weight: 400; color: var(--brand-green);
    letter-spacing: 0.2px; white-space: nowrap;
  }
  .contact {
    position: absolute; right: 27px; top: 104px;
    text-align: right; color: var(--text-light);
  }
  .contact-name { font-size: 17px; font-weight: 700; line-height: 22px; margin-bottom: 4px; }
  .contact-line {
    display: flex; justify-content: flex-end; align-items: center; gap: 6px;
    font-size: 12.5px; line-height: 19.5px;
  }
  .contact-line svg { width: 12px; height: 10px; }
  .back-brand {
    display: flex; align-items: center; gap: 14px;
    color: var(--text-light); font-size: 30px; font-weight: 400;
  }
  .back-brand .brand-mark { width: 30px; height: 30px; background: var(--text-light); }
</style>
</head>
<body>
<main class="canvas">
  <section class="card card-front" aria-label="Card front">
    <svg class="front-panel" viewBox="0 0 595 339" preserveAspectRatio="none" aria-hidden="true">
      <defs>
        <linearGradient id="panelGreen" x1="0" y1="0" x2="0" y2="1">
          <stop offset="0" stop-color="#b6dd58"/>
          <stop offset="0.35" stop-color="#abd852"/>
          <stop offset="1" stop-color="#55a826"/>
        </linearGradient>
      </defs>
      <path d="M502,0 L398,95 Q377,114 377,140 L377,205 Q377,228 395,240 L522,339 L595,339 L595,0 Z" fill="url(#panelGreen)"/>
    </svg>
    <div class="brand">
      <span class="brand-mark"></span>
      <span class="brand-name">Stonebridge Builders</span>
    </div>
    <div class="contact">
      <p class="contact-name">Your Name</p>
      <p class="contact-line">123-456-7890
        <svg viewBox="0 0 12 10" aria-label="mobile"><path d="M1,6 Q6,1 11,6 L9,7.5 L8,6 Q6,5 4,6 L3,7.5 Z" fill="#fff"/></svg>
      </p>
      <p class="contact-line">123-456-7890
        <svg viewBox="0 0 12 10" aria-label="fax"><rect x="3" y="0.5" width="6" height="3" fill="none" stroke="#fff"/><rect x="1" y="4" width="10" height="5.5" fill="#fff"/></svg>
      </p>
      <p class="contact-line">name@website.com
        <svg viewBox="0 0 12 10" aria-label="email"><rect x="0.5" y="1" width="11" height="8" fill="#fff"/><path d="M0.5,1 L6,5.5 L11.5,1" fill="none" stroke="#8ccb3e"/></svg>
      </p>
    </div>
  </section>

  <section class="card card-back" aria-label="Card back">
    <div class="back-brand">
      <span class="brand-mark"></span>
      <span>Stonebridge Builders</span>
    </div>
  </section>
</main>
</body>
</html>
```